I have a logo and need to design the business card and stationery.
Updates

The uploaded logo image named as GREYMARSH CONSTRUCTION which is to be replaced to GREYMARSH CONTRACTS. Kindly add below details and submit the designs- Company name- Greymarsh Engineering Contracts LLP Name & Post- Kelvan Joshi (Designated Partner) Address- Block No.317, Wing C, Tulvo Trade Court, Manek Pural Road, Ruparel Industrial Estate, Goregaon(E), Mumbai - 400 063 Contact- +91 97415 60382 Email- kelvanjoshi@mailbrook.example Website- www.greymarshcontracts.example Contact for Letterhead- +91-22-28754193

Hi Tovin Rahul, We are liking your Design #28860835. We have suggested some changes which are mentioned in feedback. Kindly revert with it asap to finalize this design.

Colors

Designer to choose colors to be used in the design.

```html
<!DOCTYPE html>
<html lang="en">
<head>
<meta charset="utf-8">
<title>Greymarsh Contracts – Letterhead</title>
<link href="https://fonts.googleapis.com/css2?family=Open+Sans:wght@400;600&family=Orbitron:wght@700&display=swap" rel="stylesheet">
<style>
  :root {
    --paper: #ffffff;
    --ink: #3d3d3d;
    --ink-dark: #2b2b2b;
    --band: #1f1f1f;
    --band-strip: #2e2e2e;
    --pattern: #d9d9d9;
    --signature: #cfcfcf;
  }
  html, body {
    margin: 0;
    padding: 0;
    width: 1040px;
    height: 1200px;
    overflow: hidden;
    background: var(--paper);
  }
  .letterhead {
    position: relative;
    width: 1040px;
    height: 1200px;
    background: var(--paper);
    font-family: "Open Sans", Arial, sans-serif;
    color: var(--ink);
  }
  .brand {
    position: absolute;
    top: 33px;
    left: 0;
    width: 100%;
    display: flex;
    flex-direction: column;
    align-items: center;
  }
  .brand-square {
    width: 100px;
    height: 96px;
    background: var(--ink-dark);
  }
  .brand-name {
    margin-top: 16px;
    font-family: "Open Sans", Arial, sans-serif;
    font-weight: 600;
    color: var(--ink-dark);
    text-align: center;
    line-height: 1.05;
  }
  .brand-name .line-1 { display: block; font-size: 30px; letter-spacing: 2px; }
  .brand-name .line-2 { display: block; font-size: 21px; letter-spacing: 10px; margin-left: 10px; }

  .letter {
    position: absolute;
    left: 98px;
    width: 840px;
    font-size: 15px;
  }
  .issue-date { top: 236px; }
  .recipient { top: 271px; line-height: 18px; }
  .salutation { top: 375px; }
  .body-copy { top: 428px; line-height: 27px; text-align: justify; }
  .body-copy p { margin: 0 0 27px; }
  .closing { top: 832px; }
  .signature {
    position: absolute;
    top: 868px;
    left: 98px;
    width: 240px;
    height: 26px;
    background: linear-gradient(90deg, var(--signature), rgba(207,207,207,0.2));
  }
  .signer { top: 909px; }
  .signer-name { font-size: 18px; font-weight: 600; color: var(--ink-dark); margin: 0; }
  .signer-role { font-size: 15px; margin: 6px 0 0; }

  .footer-band {
    position: absolute;
    left: 0;
    bottom: 0;
    width: 1040px;
    height: 72px;
    background: var(--band);
  }
  .footer-pattern {
    position: absolute;
    top: 4px;
    height: 64px;
    background: linear-gradient(90deg, var(--pattern), #bdbdbd);
  }
  .footer-pattern.left { left: 0; width: 212px; }
  .footer-pattern.right { right: 0; width: 212px; }
  .footer-contact {
    position: absolute;
    top: 4px;
    left: 221px;
    width: 598px;
    height: 64px;
    background: var(--band-strip);
    display: flex;
    align-items: center;
    justify-content: center;
    gap: 14px;
    color: #ffffff;
    font-family: "Orbitron", Arial, sans-serif;
    font-weight: 700;
    font-size: 27px;
    letter-spacing: 2px;
  }
  .footer-contact svg { width: 34px; height: 34px; }
</style>
</head>
<body>
<div class="letterhead">
  <header class="brand">
    <div class="brand-square"></div>
    <div class="brand-name"><span class="line-1">GREYMARSH</span><span class="line-2">CONTRACTS</span></div>
  </header>

  <div class="letter issue-date">Issuing Date: May 5, 2018</div>
  <div class="letter recipient">Name Of Employee Mr. XYZABC<br>Address of Employee<br>Address Line 2 etc..</div>
  <div class="letter salutation">Dear Mr.XYZABC</div>

  <div class="letter body-copy">
    <p>Lorem Ipsum has been the industry's standard dummy text ever since the 1500s, when an unknown printer took a galley of type and scrambled it to make a type specimen book. It has survived not only five centuries, but also the leap into electronic typesetting, remaining essentially unchanged. It was popularised in the 1960s with the release of Tavrelin sheets containing Lorem Ipsum passages, and more recently with desktop publishing software like Quillon PageForge including versions of Lorem Ipsum.</p>
    <p>Lorem Ipsum is simply dummy text of the printing and typesetting industry. Lorem Ipsum has been the industry's standard dummy text ever since the 1500s, when an unknown printer took a galley of type and scrambled it to make a type specimen book.</p>
    <p>It has survived not only five centuries, but also the leap into electronic typesetting, remaining essentially unchanged. It was popularised in the 1960s with the release of Tavrelin sheets containing Lorem IpsumIpsum passages.</p>
  </div>

  <div class="letter closing">Yours Sincerely</div>
  <div class="signature" role="img" aria-label="Handwritten signature of Anselm Pryce"></div>
  <div class="letter signer">
    <p class="signer-name">Anselm Pryce</p>
    <p class="signer-role">Managing Director</p>
  </div>

  <footer class="footer-band">
    <div class="footer-pattern left" role="img" aria-label="Repeating geometric block pattern"></div>
    <div class="footer-contact">
      <svg viewBox="0 0 36 36" aria-hidden="true">
        <rect x="2" y="2" width="32" height="32" rx="5" fill="none" stroke="#fff" stroke-width="2.5"/>
        <path d="M12 9c1-1 2.5-1 3 0l2 3.5c.5 1 0 2-.8 2.6l-1 .8c.8 2 2.5 3.8 4.5 4.6l.8-1c.6-.8 1.6-1.3 2.6-.8l3.4 2c1 .5 1 2 0 3l-1.5 1.5c-1.3 1.3-3.5 1.5-6-.2-3.3-2.2-6-5-8-8.3-1.6-2.6-1.4-4.8-.1-6z" fill="#fff"/>
      </svg>
      <span class="phone">+91 97415 60382</span>
    </div>
    <div class="footer-pattern right" role="img" aria-label="Repeating geometric block pattern"></div>
  </footer>
</div>
</body>
</html>
```